Moravel Aesthetic Doctor

I require an elegant, luxurious looking business card for my aesthetic business. I am a doctor and that will set me aside from competitors. I am planning to provide home and spa based treatments to clients with high expectations. I have attached my logo.

```html
<!DOCTYPE html>
<html lang="en">
<head>
<meta charset="utf-8">
<title>Moravel Aesthetic Doctor – Business Card</title>
<link href="https://fonts.googleapis.com/css2?family=Montserrat:wght@400;500;600&display=swap" rel="stylesheet">
<style>
  :root {
    --page: #1b1b1d;
    --card: #3a3a3d;
    --paper: #ffffff;
    --accent: #19a2e6;
    --ink-light: #f2f2f2;
    --ink-grey: #a7a7ab;
    --mark-grey: #8b8b90;
  }
  * { box-sizing: border-box; margin: 0; padding: 0; }
  html, body { width: 1200px; height: 786px; overflow: hidden; }
  body {
    background: var(--page);
    font-family: "Montserrat", Arial, sans-serif;
    position: relative;
  }
  .card {
    position: absolute;
    top: 238px;
    width: 540px;
    height: 309px;
    background: var(--card);
    overflow: hidden;
    border-radius: 3px;
    box-shadow: 0 14px 30px rgba(0,0,0,.45);
  }
  .card--front { left: 40px; }
  .card--back { left: 620px; }

  /* front */
  .front-disc { position: absolute; inset: 0; width: 540px; height: 309px; }
  .front-brand {
    position: absolute;
    left: 318px; top: 64px;
    display: flex; align-items: center; gap: 10px;
  }
  .brand-dot {
    width: 24px; height: 24px; border-radius: 50%;
    border: 2px solid var(--mark-grey);
    flex: none;
  }
  .brand-name {
    color: var(--mark-grey);
    font-weight: 400;
    font-size: 14px;
    letter-spacing: 1.5px;
    line-height: 1.3;
    text-transform: uppercase;
    white-space: nowrap;
  }
  .holder {
    position: absolute; left: 26px; top: 96px;
  }
  .holder-name {
    color: var(--accent); font-weight: 600; font-size: 14px; margin-bottom: 5px;
    white-space: nowrap;
  }
  .holder-credential {
    color: var(--ink-light); font-size: 11.5px; line-height: 1.45;
  }
  .contacts {
    position: absolute; left: 26px; bottom: 36px;
    list-style: none;
  }
  .contacts li {
    display: flex; align-items: center; gap: 8px;
    color: var(--ink-light); font-size: 11.5px; line-height: 1.7;
    letter-spacing: .3px;
  }
  .contacts svg { width: 10px; height: 10px; flex: none; }

  /* back */
  .back-brand {
    position: absolute; left: 0; right: 0; top: 78px;
    display: flex; justify-content: center; align-items: center; gap: 16px;
  }
  .back-brand .brand-dot { width: 44px; height: 44px; border-width: 2.5px; }
  .back-brand .brand-name {
    font-size: 26px; letter-spacing: 3px; color: #c9c9cd;
  }
  .services {
    position: absolute; left: 0; right: 0; top: 180px;
    text-align: center; color: var(--ink-light);
    font-size: 12.5px; line-height: 1.75; letter-spacing: .4px;
  }
  .services .sep { color: var(--accent); padding: 0 4px; }
  .services .tagline { text-transform: uppercase; letter-spacing: 1px; }
</style>
</head>
<body>
  <section class="card card--front" aria-label="Business card front">
    <svg class="front-disc" viewBox="0 0 540 309" aria-hidden="true">
      <circle cx="435" cy="60" r="165" fill="var(--paper)"/>
      <path d="M 275 0 A 171 171 0 0 0 435 231" fill="none" stroke="var(--accent)" stroke-width="4"/>
    </svg>
    <div class="front-brand">
      <span class="brand-dot"></span>
      <span class="brand-name">Moravel<br>Aesthetic Doctor</span>
    </div>
    <div class="holder">
      <p class="holder-name">Dr Elena Vorst MRCPCH MD</p>
      <p class="holder-credential">Australasian Diploma<br>of Aesthetic Medicine</p>
    </div>
    <ul class="contacts">
      <li>
        <svg viewBox="0 0 10 10"><path d="M2 0.8 L3.6 0.8 L4.2 3 L3 3.8 Q4 6 6.2 7 L7 5.8 L9.2 6.4 L9.2 8 Q9 9.4 7.6 9.2 Q1.2 8.2 0.8 2.4 Q0.8 0.8 2 0.8 Z" fill="var(--accent)"/></svg>
        0800 555 014
      </li>
      <li>
        <svg viewBox="0 0 10 10"><rect x="0.7" y="2" width="8.6" height="6" fill="none" stroke="var(--accent)" stroke-width="1"/><path d="M0.7 2 L5 5.4 L9.3 2" fill="none" stroke="var(--accent)" stroke-width="1"/></svg>
        elena@moravel.co.nz
      </li>
      <li>
        <svg viewBox="0 0 10 10"><circle cx="5" cy="5" r="4.2" fill="none" stroke="var(--accent)" stroke-width="1"/><ellipse cx="5" cy="5" rx="1.8" ry="4.2" fill="none" stroke="var(--accent)" stroke-width="0.8"/><path d="M0.8 5 H9.2" stroke="var(--accent)" stroke-width="0.8"/></svg>
        www.moravel.co.nz
      </li>
    </ul>
  </section>

  <section class="card card--back" aria-label="Business card back">
    <div class="back-brand">
      <span class="brand-dot"></span>
      <span class="brand-name">Moravel<br>Aesthetic Doctor</span>
    </div>
    <div class="services">
      <p>Dermal injectables<span class="sep">|</span>Plasma facials<span class="sep">|</span>Microneedling</p>
      <p>Skin boosters<span class="sep">|</span>Excessive sweating</p>
      <p class="tagline">Home and spa based treatments</p>
    </div>
  </section>
</body>
</html>
```